Design a Website for an IT Support Company

We are an IT support company that provides commercial IT support and services to small and medium sized businesses. We are in need of a website to be developed for our business.
We would like to work with someone who is either familiar with the IT field, or has developed a website for an IT support company in the past.
Some examples of designs/layouts that we like:
https://www.veldaworks.example/
http://www.marsbyquill.example/
http://817kq.example/
http://www.olbenstructures.example/
http://www.bykq.example/
I have attached a word document that gives a menu system/page layout format that we would like for our website as well as branch office phone numbers. Our logo is also attached that you can use for your design purposes. We currently do not have copy produced for all of the pages outlined in the word document, but would get this done during the project with the selected designer.
We would like the website to be SEO friendly & fully responsive. We would prefer a Wordpress format, however, we are open to HTML formats as well.

```html
<!DOCTYPE html>
<html lang="en">
<head>
<meta charset="utf-8">
<title>Kestrel IT – Commercial IT Support</title>
<link href="https://fonts.googleapis.com/css2?family=Exo+2:wght@300;400;500&family=Montserrat:wght@400;500;600&display=swap" rel="stylesheet">
<style>
:root{
  --blue:#0a70c4;
  --blue-deep:#075aa6;
  --blue-dark:#0b3f73;
  --sky:#e6f0fa;
  --ink:#2f3640;
  --muted:#6b7580;
  --light:#f1f4f8;
  --white:#fff;
}
*{margin:0;padding:0;box-sizing:border-box}
html,body{width:1200px;height:3279px;overflow:hidden}
body{position:relative;font-family:"Montserrat",sans-serif;color:var(--ink);background:var(--white)}
.abs{position:absolute}
h1,h2{font-weight:300}

/* header */
.topbar{left:0;top:0;width:1200px;height:44px}
.topbar-phone{right:76px;top:7px;color:var(--white);font-size:21px;font-weight:500;letter-spacing:1px;display:flex;align-items:center;gap:8px}
.socials{display:flex;gap:6px;margin-left:6px}
.social{width:28px;height:28px;border:2px solid var(--white);border-radius:50%}
.brand{display:flex;align-items:center;gap:12px;font-family:"Exo 2",sans-serif;font-weight:500;font-size:36px;color:var(--blue-dark);white-space:nowrap}
.brand-dot{width:30px;height:30px;border-radius:50%;background:var(--blue)}
.site-header .brand{left:80px;top:62px}
.nav{right:78px;top:74px;display:flex;gap:30px;align-items:center;font-size:15px;font-weight:500;color:var(--ink)}
.nav a{text-decoration:none;color:inherit}
.nav .active{background:var(--blue);color:var(--white);border-radius:22px;padding:10px 18px}

/* hero */
.hero{left:0;top:120px;width:1200px;height:560px;background:linear-gradient(90deg,#f2f6fb,var(--sky))}
.hero-photo{left:0;top:0;width:600px;height:560px;background:linear-gradient(135deg,#cfdbe6,#eef3f7 55%,#c2d2e2)}
.hero-copy{left:619px;top:108px;width:520px}
.hero-mark{width:36px;height:36px;border-radius:50%;background:var(--blue-dark)}
.hero-title{margin-top:14px;font-family:"Exo 2",sans-serif;font-weight:400;font-size:54px;line-height:58px;color:var(--blue)}
.hero-sub{margin-top:22px;font-size:17px;line-height:28px;color:var(--ink)}
.btn-pill{display:inline-block;border-radius:30px;font-family:"Exo 2",sans-serif;letter-spacing:1px}
.hero-cta{margin-top:24px;background:var(--blue);color:var(--white);padding:14px 26px;font-size:22px}
.dots{left:1152px;top:208px;display:flex;flex-direction:column;gap:14px}
.dot{width:16px;height:16px;border:2px solid var(--blue);border-radius:50%}
.dot.on{background:var(--blue)}

/* call band */
.call-band{left:0;top:680px;width:1200px;height:201px;background:var(--blue);border-top:5px solid var(--blue-dark);color:var(--white);text-align:center}
.call-band p{width:860px;margin:36px auto 0;font-size:16px;line-height:27px}
.call-line{margin-top:22px;display:flex;justify-content:center;align-items:center;gap:18px;font-size:32px;font-weight:500}

/* services */
.section-title{width:1200px;text-align:center;font-family:"Exo 2",sans-serif;font-weight:300;font-size:50px;color:var(--blue)}
.section-title span{color:var(--blue-dark)}
.services-title{left:0;top:930px}
.services-intro{left:200px;top:1000px;width:800px;text-align:center;font-size:14.5px;line-height:27px;color:var(--muted)}
.service{width:360px}
.service-art{width:180px;height:190px;margin:0 auto;border-radius:90px 90px 40px 40px;background:radial-gradient(circle at 50% 48%,#e7eaed 0 52px,#d4d9de 53px 62px,#1c7cc9 63px)}
.service-name{text-align:center;font-family:"Exo 2",sans-serif;font-weight:400;font-size:24px;letter-spacing:2px;color:var(--blue);margin:14px 0 18px}
.service-list{list-style:none}
.service-list li{display:flex;align-items:center;gap:14px;height:29.3px;font-size:14.5px;color:var(--muted);white-space:nowrap}

/* banner */
.banner{left:0;top:1709px;width:1200px;height:363px;background:linear-gradient(90deg,#0d2c5e,#3b86c8 50%,#0e3468)}

/* why */
.why{left:0;top:2072px;width:1200px;height:398px;background:var(--blue);text-align:center;color:var(--white)}
.why-title{margin-top:54px;font-family:"Exo 2",sans-serif;font-size:50px;font-weight:300;color:var(--white)}
.why-title span{color:var(--blue-dark)}
.why p{width:1040px;margin:16px auto 0;font-size:15px;line-height:27px}
.why-btn{margin-top:30px;border:2px solid var(--white);color:var(--white);padding:12px 24px;font-size:22px}

/* contact */
.contact-title{left:79px;top:2520px;font-family:"Exo 2",sans-serif;font-weight:300;font-size:44px;color:var(--blue)}
.contact-title span{color:var(--blue-dark)}
.branches{left:79px;top:2592px;list-style:none}
.branches li{display:flex;align-items:center;gap:22px;height:44.5px;font-size:17px;color:var(--muted)}
.map{left:590px;top:2536px;width:570px;height:330px;background:linear-gradient(180deg,#c9ccd0,#b5b9be);border-radius:40px 60px 30px 80px}

/* footer */
.footer{left:0;top:2880px;width:1200px;height:333px}
.footer-brand{left:77px;top:3005px;color:var(--white)}
.footer-brand .brand-dot{background:var(--white)}
.footer-social{left:128px;top:3100px;display:flex;gap:10px}
.footer-social .social{width:44px;height:44px}
.f-head{font-size:17px;font-weight:600;letter-spacing:1px;color:var(--white)}
.f-col{top:2960px;color:var(--white);font-size:14px}
.sitemap ul{list-style:none;margin-top:18px}
.sitemap li{height:32px;display:flex;align-items:center;gap:14px}
.sitemap li::before{content:"";width:8px;height:8px;border-radius:50%;background:var(--white)}
.f-contact-row{display:flex;gap:22px;align-items:flex-start;font-size:13.5px;line-height:22px}
.newsletter p{margin-top:18px;width:250px;font-size:13.5px;line-height:23px}
.news-input{margin-top:12px;width:248px;height:46px;background:var(--white);color:var(--muted);font-size:13.5px;padding:14px 10px}
.news-btn{margin-top:8px;border:2px solid var(--white);color:var(--white);padding:10px 24px;font-size:19px}
.copyright{left:0;top:3213px;width:1200px;height:66px;background:var(--light);text-align:center;line-height:66px;font-size:14px;color:var(--ink)}
</style>
</head>
<body>

<svg width="0" height="0" class="abs">
  <defs>
    <symbol id="wifi" viewBox="0 0 20 16"><g fill="none" stroke="var(--blue)" stroke-width="2" stroke-linecap="round"><path d="M2 6a11 11 0 0116 0"/><path d="M5.5 9.5a6 6 0 019 0"/></g><circle cx="10" cy="13" r="1.8" fill="var(--blue)"/></symbol>
    <symbol id="phone" viewBox="0 0 24 24"><path d="M6.6 10.8a15 15 0 006.6 6.6l2.2-2.2c.3-.3.7-.4 1-.2 1.1.4 2.3.6 3.6.6.6 0 1 .4 1 1V20c0 .6-.4 1-1 1A17 17 0 013 4c0-.6.4-1 1-1h3.5c.6 0 1 .4 1 1 0 1.3.2 2.5.6 3.6.1.3 0 .7-.2 1z"/></symbol>
  </defs>
</svg>

<!-- header -->
<header class="site-header">
  <svg class="abs topbar" width="1200" height="44" viewBox="0 0 1200 44"><path d="M790 0H1200V44H770Z" fill="var(--blue)"/></svg>
  <div class="abs topbar-phone">
    <svg width="20" height="20" fill="#fff"><use href="#phone"/></svg>
    555-010-4400
    <span class="socials"><span class="social"></span><span class="social"></span><span class="social"></span></span>
  </div>
  <div class="abs brand"><span class="brand-dot"></span>Kestrel IT</div>
  <nav class="abs nav">
    <a class="active">HOME</a><a>ABOUT US</a><a>SERVICES</a><a>WHY KESTREL IT</a><a>CONTACT</a>
  </nav>
</header>

<!-- hero -->
<section class="abs hero">
  <div class="abs hero-photo" role="img" aria-label="Overhead photo of a man working on a laptop at a white desk"></div>
  <div class="abs hero-copy">
    <div class="hero-mark"></div>
    <h1 class="hero-title">Get More From Your Technology</h1>
    <p class="hero-sub">Provides Commercial It Support And Services To Small And Medium Sized Businesses</p>
    <span class="btn-pill hero-cta">CONTACT US</span>
  </div>
  <div class="abs dots"><span class="dot"></span><span class="dot"></span><span class="dot"></span><span class="dot on"></span><span class="dot"></span></div>
</section>

<!-- call band -->
<section class="abs call-band">
  <p>Lorem Ipsum is simply dummy text of the printing and typesetting industry. Lorem Ipsum has been the industry's standard dummy text ever since the 1500s, when an unknown printer took a</p>
  <div class="call-line">Call Us On
    <svg width="58" height="58" viewBox="0 0 58 58"><circle cx="29" cy="29" r="26" fill="none" stroke="#fff" stroke-width="3"/><svg x="15" y="15" width="28" height="28" fill="#fff"><use href="#phone"/></svg></svg>
    555-010-4400
  </div>
</section>

<!-- services -->
<h2 class="abs section-title services-title">Our Best <span>Services</span></h2>
<p class="abs services-intro">Lorem Ipsum is simply dummy text of the printing and typesetting industry. Lorem Ipsum has been the industry's standard dummy text ever since the 1500s, when an unknown printer took a</p>

<div class="abs service" style="left:60px;top:1080px">
  <div class="service-art" role="img" aria-label="Illustration of a headset around a data server icon"></div>
  <div class="service-name">DATA</div>
  <ul class="service-list" style="margin-left:71px">
    <li><svg width="20" height="16"><use href="#wifi"/></svg>Managed It Services</li>
    <li><svg width="20" height="16"><use href="#wifi"/></svg>It Support &amp; Consulting</li>
    <li><svg width="20" height="16"><use href="#wifi"/></svg>It Helpdesk Services</li>
    <li><svg width="20" height="16"><use href="#wifi"/></svg>Network Security</li>
    <li><svg width="20" height="16"><use href="#wifi"/></svg>Data Backup &amp; Recovery</li>
    <li><svg width="20" height="16"><use href="#wifi"/></svg>Servers &amp; Virtualization</li>
    <li><svg width="20" height="16"><use href="#wifi"/></svg>Remote Monitoring Services</li>
    <li><svg width="20" height="16"><use href="#wifi"/></svg>Wireless Networking</li>
    <li><svg width="20" height="16"><use href="#wifi"/></svg>Email &amp; Spam Threat</li>
    <li><svg width="20" height="16"><use href="#wifi"/></svg>Management</li>
    <li><svg width="20" height="16"><use href="#wifi"/></svg>Structured Cabling</li>
  </ul>
</div>

<div class="abs service" style="left:421px;top:1080px">
  <div class="service-art" role="img" aria-label="Illustration of a headset around a microphone icon"></div>
  <div class="service-name">CLOUD</div>
  <ul class="service-list" style="margin-left:53px">
    <li><svg width="20" height="16"><use href="#wifi"/></svg>Workspace Suite Migrations</li>
    <li><svg width="20" height="16"><use href="#wifi"/></svg>Nimbus Cloud Management Services</li>
    <li><svg width="20" height="16"><use href="#wifi"/></svg>Cloud Migration Services</li>
    <li><svg width="20" height="16"><use href="#wifi"/></svg>Hosted Virtual Servers</li>
    <li><svg width="20" height="16"><use href="#wifi"/></svg>Hosted Telephone Systems</li>
  </ul>
</div>

<div class="abs service" style="left:782px;top:1080px">
  <div class="service-art" role="img" aria-label="Illustration of a headset around a cloud and router icon"></div>
  <div class="service-name">VOICE</div>
  <ul class="service-list" style="margin-left:57px">
    <li><svg width="20" height="16"><use href="#wifi"/></svg>Starline PBX Consulting</li>
    <li><svg width="20" height="16"><use href="#wifi"/></svg>Business Telephone Systems</li>
    <li><svg width="20" height="16"><use href="#wifi"/></svg>Multiple Office Phone Systems</li>
    <li><svg width="20" height="16"><use href="#wifi"/></svg>Brookline Telephone Systems</li>
    <li><svg width="20" height="16"><use href="#wifi"/></svg>SIP Trunks</li>
  </ul>
</div>

<!-- banner -->
<div class="abs banner" role="img" aria-label="Photo of a businessman standing in a blue tunnel of binary digits"></div>

<!-- why -->
<section class="abs why">
  <h2 class="why-title">Why <span>Kestrel IT</span></h2>
  <p>Lorem Ipsum is simply dummy text of the printing and typesetting industry. Lorem Ipsum has been the industry's standard dummy text ever since the 1500s, when an unknown printer took a galley of type and scrambled it to make a type specimen book. It has survived not only five centuries, but also the leap into electronic typesetting, remaining essentially unchanged. It was popularised in the 1960s with the release of Lettrafold sheets containing Lorem Ipsum passages, and more recently with desktop publishing software like Alden PageSetter including versions of Lorem Ipsum.</p>
  <span class="btn-pill why-btn">KNOW MORE</span>
</section>

<!-- contact -->
<h2 class="abs contact-title">Contact <span>Us On</span></h2>
<ul class="abs branches">
  <li><svg width="22" height="22" fill="var(--blue)"><use href="#phone"/></svg>Main Number : 555-010-4400</li>
  <li><svg width="22" height="22" fill="var(--blue)"><use href="#phone"/></svg>Houston: 555-010-4410</li>
  <li><svg width="22" height="22" fill="var(--blue)"><use href="#phone"/></svg>San Antonio : 555-010-4420</li>
  <li><svg width="22" height="22" fill="var(--blue)"><use href="#phone"/></svg>Austin : 555-010-4430</li>
  <li><svg width="22" height="22" fill="var(--blue)"><use href="#phone"/></svg>Tulsa : 555-010-4440</li>
  <li><svg width="22" height="22" fill="var(--blue)"><use href="#phone"/></svg>Oklahoma City : 555-010-4450</li>
</ul>
<div class="abs map" role="img" aria-label="Map of the United States marking Houston, San Antonio, Austin, Tulsa, Oklahoma City and the main office"></div>

<!-- footer -->
<footer>
  <svg class="abs footer" width="1200" height="333" viewBox="0 0 1200 333"><path d="M0 30Q600 -10 1200 30V333H0Z" fill="var(--blue)"/></svg>
  <div class="abs brand footer-brand"><span class="brand-dot"></span>Kestrel IT</div>
  <div class="abs footer-social"><span class="social"></span><span class="social"></span><span class="social"></span></div>

  <div class="abs f-col sitemap" style="left:345px">
    <div class="f-head">SITEMAP</div>
    <ul><li>Home</li><li>About Us</li><li>Services</li><li>Why Kestrel IT</li><li>Contact Us</li></ul>
  </div>

  <div class="abs f-col" style="left:608px">
    <div class="f-head">CONTACT US</div>
    <div class="f-contact-row" style="margin-top:20px">
      <svg width="18" height="24" viewBox="0 0 18 24"><path d="M9 0a9 9 0 00-9 9c0 7 9 15 9 15s9-8 9-15a9 9 0 00-9-9zm0 12a3 3 0 110-6 3 3 0 010 6z" fill="#fff"/></svg>
      <div><b>Kestrel IT</b><br>101 - Lorem ipsum is the simple<br>dummy text of printing Text.</div>
    </div>
    <div class="f-contact-row" style="margin-top:18px">
      <svg width="18" height="18" fill="#fff"><use href="#phone"/></svg>
      <div>555-010-4400</div>
    </div>
    <div class="f-contact-row" style="margin-top:20px">
      <svg width="18" height="14" viewBox="0 0 18 14"><rect width="18" height="14" rx="2" fill="#fff"/><path d="M1 1l8 7 8-7" fill="none" stroke="var(--blue)" stroke-width="1.5"/></svg>
      <div>info@kestrelit.example</div>
    </div>
  </div>

  <div class="abs f-col newsletter" style="left:874px">
    <div class="f-head">NEWSLETTER</div>
    <p>Would you like to receive exclusive access to articles, white papers and our regular monthly newsletter?</p>
    <div class="news-input">Enter Email Id</div>
    <span class="btn-pill news-btn">SUBSCRIBE</span>
  </div>

  <div class="abs copyright">©Kestrel IT- 2017 All Right Reserved</div>
</footer>

</body>
</html>
```